Revise Three Graphics for Company Careers website.

We have a need to find an alternative artistic approach to revising three graphics currently used on a growing companies careers/job website.
- The new art for attached graphics (named graphic #1, #2, and #3) should be clean, professional and easy to read.
- The art representing these three pieces should share common artistic elements and not necessarily look like three differently branded pieces.
- The careers site is shared between two related companies, so the colors used should complement the colors of two companies (whose logos are attached).
- Logos can be used as knock-outs if needed.
Note: Graphic #3 (currently a set of boxes 2x3) needs two additional boxes with the following copy:
- Art and Science of Communication
- Supervising 101
Lastly, Graphic #4 we need to be put into the same color font used in the two company logos. That's it!

```html
<!DOCTYPE html>
<html lang="en">
<head>
<meta charset="utf-8">
<title>Career Development Programs</title>
<link rel="stylesheet" href="https://fonts.googleapis.com/css2?family=Open+Sans:wght@400;600&display=swap">
<style>
  :root {
    --page-light: #ffffff;
    --page-mid: #f1f1f1;
    --page-edge: #dcdcdc;
    --frame-line: #9a9a9a;
    --navy: #154c88;
    --rose: #b96876;
    --lime: #9bcb05;
    --sky: #4acbe6;
    --teal-ring: #3aaebf;
    --ink: #1d3a66;
    --white: #ffffff;
  }
  * { box-sizing: border-box; margin: 0; padding: 0; }
  html, body { width: 849px; height: 1200px; overflow: hidden; }
  body {
    font-family: "Open Sans", "Segoe UI", sans-serif;
    background: var(--page-mid);
  }
  .canvas {
    position: relative;
    width: 849px;
    height: 1200px;
    background: radial-gradient(ellipse 75% 60% at 50% 52%, var(--page-light) 0%, var(--page-mid) 60%, var(--page-edge) 100%);
    border-left: 2px solid var(--frame-line);
    border-top: 1px solid #c8c8c8;
  }
  .program {
    position: absolute;
    width: 178px;
    height: 178px;
    margin: -89px 0 0 -89px;
    border-radius: 50%;
    display: flex;
    align-items: center;
    justify-content: center;
    text-align: center;
    padding: 0 14px;
    font-size: 17.5px;
    line-height: 1.5;
    box-shadow: 3px 5px 12px rgba(0, 0, 0, 0.28);
  }
  .program--filled { color: var(--white); font-weight: 600; letter-spacing: -0.3px; }
  .program--outline {
    background: var(--white);
    border: 4px solid var(--teal-ring);
    color: var(--ink);
    font-weight: 400;
  }
  .program--navy { background: var(--navy); }
  .program--rose { background: var(--rose); }
  .program--lime { background: var(--lime); }
  .program--sky { background: var(--sky); }
</style>
</head>
<body>
  <main class="canvas">
    <div class="program program--filled program--navy" style="left:127px;top:506px">Scientific Lunch<br>&amp; Learns</div>
    <div class="program program--outline" style="left:317px;top:506px">Statistics in<br>Pharmaceutical<br>Development<br>Workshop</div>
    <div class="program program--filled program--rose" style="left:517px;top:506px">Conferences &amp;<br>Seminars</div>
    <div class="program program--outline" style="left:707px;top:506px">Leadership<br>Development</div>

    <div class="program program--outline" style="left:124px;top:695px">Creating the Right<br>Team Workshop</div>
    <div class="program program--filled program--lime" style="left:315px;top:695px">Project<br>Management<br>Training</div>
    <div class="program program--outline" style="left:528px;top:697px">Art and Science<br>of<br>Communication</div>
    <div class="program program--filled program--sky" style="left:719px;top:697px">Supervising 101</div>
  </main>
</body>
</html>
```